New Business Card Design Project

I need a design for business cards, i am an electrical business called "Corvane Electrical and Communications" i need the cards to be double sided with the company logo on the back (attached) the front needs to say my company name, web site, email address, telephone number, and ABN number and electrical license number. I am open to different arrangements of the information but would like the background to be incorporating something electrical or something that looks smart. open to all additional ideas also.

The company colours are orange and grey see logo attached.

Business Name: Corvane Electrical and Communications
Website: corvaneelectricalandcomms.example.com.au
Email: brent@corvaneelectricalandcomms.example.com.au
Telephone(mobile): 0481209736
ABN: 71208349162
Lic No: 418273D

Target Market(s)

Business entities, Project Managers, Accounts, Clients

Industry/Entity Type

Electrician

Contact Information for Business Card

I need a design for business cards, i am an electrical business called "Corvane Electrical and Communications" i need the cards to be double sided with the company logo on the back (attached) the front needs to say my company name

Font styles to use
Serif
Sans Serif

Colors
f37122
5c5c5c

Requirements
Must have
• Must have the Logo on the back open to different ways of it being on the back but had in mind to keep it central but again open to other options
Nice to have
• A real modern cool background that is eye catching yet contemporary
Should not have
• No backgrounds of a light bulb or plug or anything like that

```html
<!DOCTYPE html>
<html lang="en">
<head>
<meta charset="utf-8">
<title>Corvane Electrical and Communications – Business Cards</title>
<link rel="stylesheet" href="https://fonts.googleapis.com/css2?family=Play:wght@400;700&family=Open+Sans:wght@400;600&display=swap">
<style>
  :root {
    --backdrop: #3b3b3c;
    --card: #58585a;
    --accent: #f7a81b;
    --ink: #ffffff;
    --ink-soft: #ececec;
    --divider: #7a7a7c;
  }
  * { box-sizing: border-box; margin: 0; padding: 0; }
  html, body {
    width: 1105px;
    height: 1200px;
    overflow: hidden;
    background: var(--backdrop);
  }
  .sheet {
    position: relative;
    width: 1105px;
    height: 1200px;
  }
  .card {
    position: absolute;
    left: 196px;
    width: 720px;
    height: 411px;
    background: var(--card);
    color: var(--ink);
  }
  .card--front { top: 146px; }
  .card--back  { top: 602px; }

  /* Brand name block */
  .brand {
    font-family: "Play", sans-serif;
    font-weight: 700;
    color: var(--ink);
    text-transform: uppercase;
    line-height: 1;
    text-align: center;
  }
  .brand__name { display: block; }
  .brand__line { display: block; }

  .card--front .brand {
    position: absolute;
    left: 34px;
    top: 150px;
    width: 270px;
  }
  .card--front .brand__name { font-size: 50px; letter-spacing: 3px; }
  .card--front .brand__line { font-size: 12.5px; letter-spacing: 0.4px; margin-top: 10px; }

  .divider {
    position: absolute;
    left: 326px;
    top: 102px;
    width: 1px;
    height: 222px;
    background: var(--divider);
  }

  .contact {
    position: absolute;
    left: 355px;
    top: 104px;
    font-family: "Play", sans-serif;
  }
  .contact__name {
    font-size: 25px;
    font-weight: 700;
    color: var(--accent);
    line-height: 1.1;
  }
  .contact__role {
    font-size: 18px;
    font-weight: 700;
    color: var(--ink);
    margin-top: 2px;
  }
  .contact__ids {
    margin-top: 22px;
    font-size: 18px;
    line-height: 28px;
    color: var(--ink-soft);
  }
  .contact__list {
    list-style: none;
    margin-top: 10px;
  }
  .contact__item {
    display: flex;
    align-items: center;
    gap: 8px;
    height: 28px;
    font-size: 18px;
    color: var(--ink-soft);
  }
  .contact__item--small { font-size: 13.5px; letter-spacing: -0.2px; }
  .contact__icon { width: 18px; height: 18px; flex: none; }

  .card--back .brand {
    position: absolute;
    left: 0;
    top: 150px;
    width: 720px;
  }
  .card--back .brand__name { font-size: 92px; letter-spacing: 6px; }
  .card--back .brand__line { font-size: 21px; letter-spacing: 0.8px; margin-top: 14px; }

  .card__web {
    position: absolute;
    left: 0;
    top: 330px;
    width: 720px;
    text-align: center;
    font-family: "Open Sans", sans-serif;
    font-weight: 600;
    font-size: 17px;
    letter-spacing: 0.6px;
    color: var(--ink);
  }
</style>
</head>
<body>
<main class="sheet">

  <section class="card card--front" aria-label="Business card front">
    <div class="brand">
      <span class="brand__name">Corvane</span>
      <span class="brand__line">Electrical &amp; Communications</span>
    </div>

    <div class="divider"></div>

    <div class="contact">
      <p class="contact__name">Dara Whitlow</p>
      <p class="contact__role">CEO/Founder</p>
      <p class="contact__ids">ABN: 71208349162<br>Lic No: 418273D</p>
      <ul class="contact__list">
        <li class="contact__item">
          <svg class="contact__icon" viewBox="0 0 18 18" aria-hidden="true">
            <rect x="4.5" y="1" width="9" height="16" rx="1.6" fill="var(--accent)"/>
            <rect x="6" y="3" width="6" height="10" fill="var(--card)"/>
            <circle cx="9" cy="15" r="0.9" fill="var(--card)"/>
          </svg>
          0481209736
        </li>
        <li class="contact__item contact__item--small">
          <svg class="contact__icon" viewBox="0 0 18 18" aria-hidden="true">
            <rect x="1.5" y="4" width="15" height="10" fill="var(--accent)"/>
            <path d="M1.5 4 L9 10 L16.5 4" fill="none" stroke="var(--card)" stroke-width="1.3"/>
          </svg>
          brent@corvaneelectricalandcomms.example.com.au
        </li>
        <li class="contact__item contact__item--small">
          <svg class="contact__icon" viewBox="0 0 18 18" aria-hidden="true">
            <circle cx="9" cy="9" r="7.5" fill="var(--accent)"/>
            <ellipse cx="9" cy="9" rx="3.2" ry="7.5" fill="none" stroke="var(--card)" stroke-width="1"/>
            <line x1="1.5" y1="9" x2="16.5" y2="9" stroke="var(--card)" stroke-width="1"/>
          </svg>
          corvaneelectricalandcomms.example.com.au
        </li>
      </ul>
    </div>
  </section>

  <section class="card card--back" aria-label="Business card back">
    <div class="brand">
      <span class="brand__name">Corvane</span>
      <span class="brand__line">Electrical &amp; Communications</span>
    </div>
    <p class="card__web">www.corvaneelectricalandcomms.example.com.au</p>
  </section>

</main>
</body>
</html>
```